Request for Business Card Design

Hi. My name is Marlene, I am looking for a new business card design for my company, Quarrow Signal Instruments, LLC. I really like the design you did for Tarsel Venture and was hoping you could do something similar using our full logo and our mark. I am also open to any raised texture design using our mark. I have attached our full logo, which would need to be somewhere on the card, as well as the mark in both outline and full form, as well as our brand colors / guide. The card does not have to be white, as long as our logo and mark appear. I actually like darker colored business cards more, but am open to all options. If you are interested in working with me, please let me know. We would also take the business card design into letterhead design if you can do that.

```html
<!DOCTYPE html>
<html lang="en">
<head>
<meta charset="utf-8">
<title>Quarrow Signal Instruments – Business Card</title>
<link rel="stylesheet" href="https://fonts.googleapis.com/css2?family=Poppins:wght@400;500;600&display=swap">
<style>
  :root {
    --page-bg: #e9e7e8;
    --card-dark: #3f4044;
    --accent-blue: #0f9cc6;
    --frost-light: #f1e9ea;
    --frost-mid: #e2d4d6;
    --text-light: #ffffff;
    --text-dark: #3f4044;
  }
  * { box-sizing: border-box; margin: 0; padding: 0; }
  html, body {
    width: 1200px;
    height: 900px;
    overflow: hidden;
    background: var(--page-bg);
    font-family: "Poppins", sans-serif;
  }
  .card {
    position: absolute;
    left: 120px;
    top: 153px;
    width: 960px;
    height: 593px;
    overflow: hidden;
    background: linear-gradient(160deg, var(--frost-light) 0%, var(--frost-mid) 100%);
    box-shadow: 0 18px 40px rgba(0, 0, 0, 0.18);
  }
  .card-shapes {
    position: absolute;
    inset: 0;
    width: 100%;
    height: 100%;
  }
  .brand {
    position: absolute;
    left: 50px;
    top: 140px;
    display: flex;
    align-items: center;
    gap: 18px;
  }
  .brand-dot {
    width: 62px;
    height: 62px;
    border-radius: 50%;
    background: var(--accent-blue);
    flex: none;
  }
  .brand-name {
    font-weight: 600;
    font-size: 26px;
    line-height: 1.15;
    color: var(--text-dark);
    letter-spacing: 0.5px;
  }
  .contact {
    position: absolute;
    left: 523px;
    top: 110px;
    color: var(--text-light);
  }
  .person-name {
    font-weight: 600;
    font-size: 39px;
    line-height: 1.1;
    color: var(--accent-blue);
    letter-spacing: 0.3px;
  }
  .person-title {
    font-weight: 400;
    font-size: 27px;
    line-height: 1.3;
    margin-left: -2px;
  }
  .address {
    margin-top: 40px;
    font-size: 27px;
    line-height: 35px;
  }
  .channels {
    margin-top: 42px;
    list-style: none;
    font-size: 27px;
    line-height: 35px;
  }
  .channels li {
    display: flex;
    align-items: center;
    gap: 9px;
  }
  .channels svg {
    width: 25px;
    height: 25px;
    flex: none;
  }
</style>
</head>
<body>
  <div class="card">
    <svg class="card-shapes" viewBox="0 0 1090 673" preserveAspectRatio="none" aria-hidden="true">
      <path fill="var(--accent-blue)" d="M479,0 L524,0 C560,60 560,200 520,300 C490,380 470,440 464,510 C468,430 496,350 516,280 C540,180 528,70 479,0 Z"/>
      <path fill="var(--card-dark)" d="M524,0 C560,60 560,200 520,300 C480,400 455,470 462,560 C466,610 484,650 502,673 L1090,673 L1090,0 Z"/>
    </svg>

    <div class="brand">
      <span class="brand-dot"></span>
      <span class="brand-name">QUARROW SIGNAL<br>INSTRUMENTS</span>
    </div>

    <div class="contact">
      <h1 class="person-name">MARLENE HOLLIS</h1>
      <p class="person-title">Managing Director</p>
      <p class="address">421, Address line<br>goes here<br>45452,Country Name</p>
      <ul class="channels">
        <li>
          <svg viewBox="0 0 24 24" aria-hidden="true"><path fill="var(--accent-blue)" d="M6.6 10.8a15.1 15.1 0 0 0 6.6 6.6l2.2-2.2a1 1 0 0 1 1-.25 11.4 11.4 0 0 0 3.6.57 1 1 0 0 1 1 1V20a1 1 0 0 1-1 1A17 17 0 0 1 3 4a1 1 0 0 1 1-1h3.5a1 1 0 0 1 1 1c0 1.25.2 2.45.57 3.57a1 1 0 0 1-.25 1z"/></svg>
          044-555 019 274
        </li>
        <li>
          <svg viewBox="0 0 24 24" aria-hidden="true"><path fill="var(--accent-blue)" d="M2 5h20v14H2z M2 5l10 8 10-8" stroke="var(--card-dark)" stroke-width="1.4"/></svg>
          info@quarrowsignal.com
        </li>
        <li>
          <svg viewBox="0 0 24 24" aria-hidden="true"><g fill="none" stroke="var(--accent-blue)" stroke-width="1.8"><circle cx="12" cy="12" r="9.5"/><ellipse cx="12" cy="12" rx="4" ry="9.5"/><path d="M2.5 12h19M4 7h16M4 17h16"/></g></svg>
          www.quarrowsignal.com
        </li>
      </ul>
    </div>
  </div>
</body>
</html>
```